Web design required

1-We need a web design for existing company based in New Zealand
2-We build residential house and light commercial
3-We has in-house designer which allow us can provide interior design
4-We modeling project before site construction, which enable both client and construction team to visually analysis whole project,

Target Market(s)

middle class residential house market
Ref: http://www.parvellbuilders.co.nz/

Industry/Entity Type

Construction Company

Number of Pages Required

1 page

Font styles to use
Sans Serif
Other font styles liked:
• Such as : Central Gothic or similar which has more design taste

Colors

Designer to choose colors to be used in the design.

Requirements
Must have
• Front sheet, contact information, sample project

```html
<!DOCTYPE html>
<html lang="en">
<head>
<meta charset="utf-8">
<title>Harbourline Homes</title>
<link href="https://fonts.googleapis.com/css2?family=Lato:wght@300;400;700;900&display=swap" rel="stylesheet">
<style>
:root{
  --blue:#0b67ae;
  --blue-dark:#08528c;
  --ink:#1f1f1f;
  --text:#444;
  --muted:#777;
  --light:#e9e9e9;
  --dark:#161616;
  --darker:#0d0d0d;
  --white:#fff;
}
*{box-sizing:border-box;margin:0;padding:0}
html,body{width:1200px;height:3352px;overflow:hidden}
body{font-family:'Lato',sans-serif;color:var(--text);background:var(--white);position:relative}
.abs{position:absolute}
a{color:inherit;text-decoration:none}

/* top bar */
.topbar{top:0;left:0;width:1200px;height:45px;border-bottom:1px solid #e2e2e2;font-size:15px;color:#555}
.topbar .item{top:13px;display:flex;align-items:center;gap:10px}
.topbar .social{top:14px;right:78px;display:flex;gap:12px}
.dot{width:14px;height:14px;border-radius:50%;background:#777;display:block}

/* header */
.header{top:45px;left:0;width:1200px;height:111px;border-bottom:1px solid #e5e5e5}
.brand{left:78px;top:34px;display:flex;align-items:center;gap:14px}
.brand-mark{width:44px;height:44px;background:var(--blue)}
.brand-name{font-weight:700;font-size:30px;letter-spacing:2px;color:var(--blue)}
.nav{right:78px;top:40px;display:flex;gap:40px;font-size:16px;color:#333}
.nav .active{color:var(--blue);position:relative}
.nav .active::after{content:"";position:absolute;left:-6px;right:-6px;top:68px;height:4px;background:var(--blue)}

/* hero */
.hero{top:156px;left:0;width:1200px;height:573px;background:linear-gradient(120deg,#6a6f73 0%,#a49b82 35%,#8d8f8e 60%,#5f6367 100%)}
.hero-shade{inset:0;background:rgba(0,0,0,.18)}
.hero h1{top:224px;width:1200px;text-align:center;color:#fff;font-weight:900;font-size:43px;letter-spacing:.5px}
.hero .rule{top:287px;left:566px;width:68px;height:3px;background:#fff}
.hero p{top:302px;left:310px;width:580px;text-align:center;color:#fff;font-size:18px;line-height:28px}
.btn{display:inline-block;font-size:17px;padding:0 28px;line-height:44px;height:44px;color:#fff}
.btn-blue{background:var(--blue)}
.btn-ghost{border:2px solid #fff;line-height:40px}
.hero .actions{top:366px;left:0;width:1200px;display:flex;justify-content:center;gap:8px}

/* section headings */
.heading{text-align:center;width:100%}
.heading svg{display:block;margin:0 auto}
.heading h2{font-weight:700;font-size:38px;color:var(--ink);letter-spacing:.5px;margin-top:12px;line-height:44px}
.heading .sub{font-size:16px;color:#333;margin-top:4px;letter-spacing:.5px}
.heading .bar{width:96px;height:4px;background:var(--blue);margin:26px auto 0}

/* about */
.about{top:729px;left:0;width:1200px;height:545px}
.about .photo-back{left:78px;top:53px;width:311px;height:416px;background:linear-gradient(135deg,#c9a22a,#e2c76a 45%,#b7b3a4)}
.about .frame-back{left:96px;top:69px;width:274px;height:383px;border:3px solid rgba(255,255,255,.85)}
.about .photo-front{left:230px;top:122px;width:235px;height:290px;background:linear-gradient(160deg,#d9d6cc,#c9863d 55%,#6d7478);border:8px solid #fff;box-shadow:0 0 0 1px #ddd}
.about .copy{left:528px;top:105px;width:570px}
.about .copy p{font-size:14px;line-height:25px;color:#444;text-align:center;margin-top:42px}
.about .copy .btn{display:block;margin:28px auto 0;width:170px;text-align:center;padding:0}

/* offer */
.offer{top:1274px;left:0;width:1200px;height:507px;background:var(--light)}
.offer .heading{position:absolute;top:44px}
.service{top:219px;width:340px;text-align:center}
.service .icon{width:105px;height:105px;background:var(--blue);margin:0 auto;display:flex;align-items:center;justify-content:center}
.service h3{font-weight:400;font-size:29px;color:var(--ink);margin-top:18px}
.service p{font-size:14px;line-height:25px;color:#444;margin:2px auto 0;width:290px}

/* projects */
.projects{top:1781px;left:0;width:1200px;height:626px;background:linear-gradient(110deg,#1b1b1b,#2c2623 50%,#3a261c 100%)}
.projects .shade{inset:0;background:rgba(0,0,0,.45)}
.projects .heading{position:absolute;top:44px}
.projects .heading h2,.projects .heading .sub{color:#fff}
.filters{top:228px;left:0;width:1200px;display:flex;justify-content:center;align-items:center;gap:32px;font-size:14px;color:#999;letter-spacing:.5px}
.filters .line{width:36px;height:2px;background:var(--blue)}
.filters .on{color:#fff}
.tile{top:282px;width:261px;height:250px}
.tile-hover{border:8px solid var(--blue);background:rgba(14,40,35,.82);display:flex;flex-direction:column;align-items:center;justify-content:center;gap:14px;color:#fff;font-size:27px}
.arrow{top:557px;width:24px;height:24px;background:#4b4b4b;display:flex;align-items:center;justify-content:center}

/* news */
.news{top:2407px;left:0;width:1200px;height:642px}
.news .heading{position:absolute;top:44px}
.card{top:219px;width:333px}
.card .img{height:248px;position:relative}
.card .date{position:absolute;left:0;top:0;width:76px;height:100px;background:var(--blue);color:#fff;text-align:center;padding-top:14px}
.card .date b{display:block;font-weight:400;font-size:36px;line-height:38px}
.card .date span{font-size:16px}
.card h4{color:var(--blue);font-weight:700;font-size:21px;line-height:31px;margin-top:16px;width:310px}
.card p{font-size:14px;line-height:24px;color:#777;margin-top:4px;width:290px}
.card p .more{color:var(--blue);font-weight:700;font-size:18px;margin-left:6px}

/* footer */
.footer{top:3049px;left:0;width:1200px;height:250px;background:var(--dark);color:#ddd}
.footer h5{font-weight:400;font-size:29px;color:#fff}
.links{left:78px;top:30px}
.links ul{list-style:none;font-size:14px;line-height:26px;margin-top:12px}
.links li{display:flex;align-items:center;gap:10px}
.links .b{width:12px;height:12px;border-radius:50%;background:#ddd}
.cols{display:flex;gap:40px}
.tweets{left:412px;top:30px;width:300px}
.tweet{display:flex;gap:12px;margin-top:18px;font-size:13.5px;line-height:20px}
.tweet div{width:250px}
.tweet .t{color:#888}
.contact{left:790px;top:30px}
.contact .row{display:flex;gap:16px;font-size:15px;line-height:22px;margin-top:14px;align-items:flex-start}
.bottombar{top:3299px;left:0;width:1200px;height:53px;background:var(--darker);color:#ccc;font-size:14px}
.bottombar .copy{left:78px;top:18px}
.bottombar .social{right:78px;top:20px;display:flex;gap:26px}
.bottombar .social .dot{background:#888}
.totop{left:573px;top:3259px;width:54px;height:40px;background:#2d2d2d;clip-path:polygon(20% 0,80% 0,100% 100%,0 100%);display:flex;align-items:center;justify-content:center}
</style>
</head>
<body>

<!-- top bar -->
<div class="abs topbar">
  <div class="abs item" style="left:78px">
    <svg width="20" height="15" viewBox="0 0 20 15"><rect width="20" height="15" fill="#0b67ae"/><path d="M0 0l10 8 10-8" stroke="#fff" fill="none" stroke-width="1.5"/></svg>
    Call Us Now 09 555 0142
  </div>
  <div class="abs item" style="left:348px">
    <svg width="18" height="18" viewBox="0 0 24 24"><path fill="#0b67ae" d="M6.6 10.8a15 15 0 006.6 6.6l2.2-2.2a1 1 0 011-.25 11.4 11.4 0 003.6.57 1 1 0 011 1V20a1 1 0 01-1 1A17 17 0 013 4a1 1 0 011-1h3.5a1 1 0 011 1c0 1.25.2 2.45.57 3.6a1 1 0 01-.25 1z"/></svg>
    info@harbourlinehomes.com
  </div>
  <div class="abs social"><i class="dot"></i><i class="dot"></i><i class="dot"></i><i class="dot"></i></div>
</div>

<!-- header -->
<header class="abs header">
  <div class="abs brand"><span class="brand-mark"></span><span class="brand-name">HARBOURLINE HOMES</span></div>
  <nav class="abs nav">
    <a class="active">HOME</a><a>ABOUT</a><a>SERVICES</a><a>PROJECTS</a><a>NEWS</a><a>CONTACT</a>
  </nav>
</header>

<!-- hero -->
<section class="abs hero" role="img" aria-label="Two builders in hard hats reviewing plans on a tablet at a construction site">
  <div class="abs hero-shade"></div>
  <h1 class="abs">DESIGN YOUR DREAMS WITH US</h1>
  <div class="abs rule"></div>
  <p class="abs">Creating a sustainable future through building preservation green architecture, and smart design</p>
  <div class="abs actions"><a class="btn btn-blue">CONTACT US</a><a class="btn btn-ghost">VIEW PROJECTS</a></div>
</section>

<!-- about -->
<section class="abs about">
  <div class="abs photo-back" role="img" aria-label="Hard hat and plans on a desk"></div>
  <div class="abs frame-back"></div>
  <div class="abs photo-front" role="img" aria-label="Two engineers in safety vests and hard hats"></div>
  <div class="abs copy">
    <div class="heading">
      <svg width="84" height="22" viewBox="0 0 84 22"><path d="M2 20L42 4l40 16" stroke="#0b67ae" stroke-width="7" fill="none"/></svg>
      <h2>WHO WE ARE</h2>
      <div class="sub">WELCOME TO HARBOURLINE HOMES</div>
    </div>
    <p>Lorem Ipsum is simply dummy text of the printing and typesetting industry. Lorem Ipsum has been the industry's standard dummy text ever since the 1500s, when an unknown printer took a galley of type and scrambled it to make a type specimen book. It has survived not only five centuries, but also the leap into electronic typesetting, remaining essentially unchanged.</p>
    <a class="btn btn-blue">KNOW MORE</a>
  </div>
</section>

<!-- offer -->
<section class="abs offer">
  <div class="heading">
    <svg width="84" height="22" viewBox="0 0 84 22"><path d="M2 20L42 4l40 16" stroke="#0b67ae" stroke-width="7" fill="none"/></svg>
    <h2>WHAT WE OFFER</h2>
    <div class="sub">ALWAYS DEDICATED AND DEVOTED</div>
    <div class="bar"></div>
  </div>
  <div class="abs service" style="left:67px">
    <div class="icon"><svg width="46" height="42" viewBox="0 0 46 42"><path d="M23 3L3 21h6v18h10V28h8v11h10V21h6z" fill="#fff"/></svg></div>
    <h3>Residential</h3>
    <p>Lorem Ipsum is simply dummy text of the printing and typesetting industry. Lorem Ipsum has been the industry</p>
  </div>
  <div class="abs service" style="left:429px">
    <div class="icon"><svg width="44" height="44" viewBox="0 0 44 44"><path fill="#fff" d="M6 40V10h14V4h18v36z"/><g fill="#0b67ae"><rect x="10" y="15" width="4" height="4"/><rect x="10" y="23" width="4" height="4"/><rect x="10" y="31" width="4" height="4"/><rect x="24" y="9" width="4" height="4"/><rect x="31" y="9" width="4" height="4"/><rect x="24" y="17" width="4" height="4"/><rect x="31" y="17" width="4" height="4"/><rect x="24" y="25" width="4" height="4"/><rect x="31" y="25" width="4" height="4"/><rect x="27" y="33" width="5" height="7"/></g></svg></div>
    <h3>Commercial</h3>
    <p>Lorem Ipsum is simply dummy text of the printing and typesetting industry. Lorem Ipsum has been the industry</p>
  </div>
  <div class="abs service" style="left:791px">
    <div class="icon"><svg width="46" height="42" viewBox="0 0 46 42"><path d="M23 3L3 21h6v18h28V21h6z" fill="none" stroke="#fff" stroke-width="3.5"/><path d="M17 22l12 12M29 22L17 34" stroke="#fff" stroke-width="3.5"/></svg></div>
    <h3>Interior design</h3>
    <p>Lorem Ipsum is simply dummy text of the printing and typesetting industry. Lorem Ipsum has been the industry</p>
  </div>
</section>

<!-- projects -->
<section class="abs projects" role="img" aria-label="Dark backdrop of builders in hard hats">
  <div class="abs shade"></div>
  <div class="heading">
    <svg width="84" height="22" viewBox="0 0 84 22"><path d="M2 20L42 4l40 16" stroke="#0b67ae" stroke-width="7" fill="none"/></svg>
    <h2>LASTEST PROJECTS</h2>
    <div class="sub">EXPERIENCE &amp; CREATIVITY HOUSE</div>
  </div>
  <div class="abs filters"><span class="line"></span><span class="on">ALL</span><span>RESIDENTIAL</span><span>COMMERCIAL</span><span>INTERIOR DESIGN</span><span class="line"></span></div>
  <div class="abs tile" style="left:78px;background:linear-gradient(180deg,#7fa0bd 0%,#b79a78 45%,#8a4f3a 75%,#5a6b3c 100%)" role="img" aria-label="Two-storey family home with brick driveway"></div>
  <div class="abs tile" style="left:339px;background:linear-gradient(120deg,#c8ced3,#8f9aa3 50%,#e6e5e0)" role="img" aria-label="Bright living room with floor-to-ceiling windows"></div>
  <div class="abs tile tile-hover" style="left:600px" role="img" aria-label="Interior design project highlighted">
    <svg width="40" height="24" viewBox="0 0 40 24"><path d="M2 12C10 2 30 2 38 12 30 22 10 22 2 12z" fill="none" stroke="#fff" stroke-width="2.5"/><circle cx="20" cy="12" r="5" fill="#fff"/></svg>
    <span>Interior design</span>
    <svg width="28" height="28" viewBox="0 0 28 28"><path d="M12 16l4-4M10 12l-5 5a4 4 0 006 6l5-5M18 16l5-5a4 4 0 00-6-6l-5 5" stroke="#fff" stroke-width="3" fill="none"/></svg>
  </div>
  <div class="abs tile" style="left:861px;background:linear-gradient(160deg,#d6d6d2,#9a9893 55%,#c7b35a)" role="img" aria-label="Modern cafe interior with tables and chairs"></div>
  <div class="abs arrow" style="left:78px"><svg width="8" height="12" viewBox="0 0 8 12"><path d="M6 1L1 6l5 5" stroke="#ccc" stroke-width="2" fill="none"/></svg></div>
  <div class="abs arrow" style="left:1098px"><svg width="8" height="12" viewBox="0 0 8 12"><path d="M2 1l5 5-5 5" stroke="#ccc" stroke-width="2" fill="none"/></svg></div>
</section>

<!-- news -->
<section class="abs news">
  <div class="heading">
    <svg width="84" height="22" viewBox="0 0 84 22"><path d="M2 20L42 4l40 16" stroke="#0b67ae" stroke-width="7" fill="none"/></svg>
    <h2>LATEST NEWS</h2>
    <div class="sub">CONNECT WITH US ALL ABOUT HARBOURLINE</div>
    <div class="bar"></div>
  </div>
  <article class="abs card" style="left:78px">
    <div class="img" style="background:linear-gradient(150deg,#aebfd2,#6d7c8a 55%,#2c3440)" role="img" aria-label="Businessman on a balcony overlooking a construction site">
      <div class="date"><b>29</b><span>APR</span></div>
    </div>
    <h4>Lorem Ipsum is simply dummy text of the...</h4>
    <p>Lorem Ipsum is simply dummy text of the printing and typesetting industry...<span class="more">»</span></p>
  </article>
  <article class="abs card" style="left:434px">
    <div class="img" style="background:linear-gradient(180deg,#23354f,#3b5478 50%,#c9b48a 80%,#4d4a44)" role="img" aria-label="Modern commercial building lit at dusk">
      <div class="date"><b>29</b><span>APR</span></div>
    </div>
    <h4>Lorem Ipsum is simply dummy text of the...</h4>
    <p>Lorem Ipsum is simply dummy text of the printing and typesetting industry...<span class="more">»</span></p>
  </article>
  <article class="abs card" style="left:789px">
    <div class="img" style="background:linear-gradient(180deg,#d9e2ea,#b98a5e 45%,#8d8f86 75%,#6b7d4a)" role="img" aria-label="Multi-storey apartment building with balconies">
      <div class="date"><b>29</b><span>APR</span></div>
    </div>
    <h4>Lorem Ipsum is simply dummy text of the...</h4>
    <p>Lorem Ipsum is simply dummy text of the printing and typesetting industry...<span class="more">»</span></p>
  </article>
</section>

<!-- footer -->
<footer class="abs footer">
  <div class="abs links">
    <h5>Links</h5>
    <div class="cols">
      <ul><li><i class="b"></i>Home</li><li><i class="b"></i>About Us</li><li><i class="b"></i>Services</li><li><i class="b"></i>Projects</li></ul>
      <ul><li><i class="b"></i>News</li><li><i class="b"></i>Contact Us</li></ul>
    </div>
  </div>
  <div class="abs tweets">
    <h5>Recent tweets</h5>
    <div class="tweet"><svg width="20" height="16" viewBox="0 0 20 16"><path d="M2 10l7 4 9-12" stroke="#aaa" stroke-width="2.5" fill="none"/></svg><div>@mattrewi @harbourlinehomes <span class="t">Thank you very much..</span><br><span class="t">4 days ago</span></div></div>
    <div class="tweet"><svg width="20" height="16" viewBox="0 0 20 16"><path d="M2 10l7 4 9-12" stroke="#aaa" stroke-width="2.5" fill="none"/></svg><div>@mattrewi @harbourlinehomes <span class="t">Thank you very much..</span><br><span class="t">4 days ago</span></div></div>
  </div>
  <div class="abs contact">
    <h5>Contact Info</h5>
    <div class="row"><svg width="16" height="22" viewBox="0 0 16 22"><path d="M8 0a8 8 0 00-8 8c0 6 8 14 8 14s8-8 8-14a8 8 0 00-8-8zm0 11a3 3 0 110-6 3 3 0 010 6z" fill="#fff"/></svg><span>14 Kauri Lane, Riverhead, Auckland<br>0820</span></div>
    <div class="row"><svg width="18" height="18" viewBox="0 0 24 24"><path fill="#fff" d="M6.6 10.8a15 15 0 006.6 6.6l2.2-2.2a1 1 0 011-.25 11.4 11.4 0 003.6.57 1 1 0 011 1V20a1 1 0 01-1 1A17 17 0 013 4a1 1 0 011-1h3.5a1 1 0 011 1c0 1.25.2 2.45.57 3.6a1 1 0 01-.25 1z"/></svg><span>09 555 0142</span></div>
    <div class="row"><svg width="18" height="14" viewBox="0 0 18 14"><rect x="1" y="1" width="16" height="12" fill="none" stroke="#fff" stroke-width="2"/><path d="M1 1l8 6 8-6" stroke="#fff" stroke-width="2" fill="none"/></svg><span>info@harbourlinehomes.com</span></div>
  </div>
</footer>
<div class="abs totop"><svg width="16" height="10" viewBox="0 0 16 10"><path d="M2 8l6-6 6 6" stroke="#ccc" stroke-width="2.5" fill="none"/></svg></div>
<div class="abs bottombar">
  <div class="abs copy">2017 ©HARBOURLINE HOMES. - All Rights Reserved.</div>
  <div class="abs social"><i class="dot"></i><i class="dot"></i><i class="dot"></i></div>
</div>

</body>
</html>
```